Redesign company trifold brochure

We are rebranding our company in September and looking for a more professional design for our brochure.

What we do - providing interdisciplinary care for those supporting ill, elderly and special needs pets at home following the human hospice model of care - is very novel and our brochure is key in explaining it and our offerings.

We serve dogs and cats. Most of the animals are quite sick, elderly. I have many personal and stock photos we can use in the brochure. Please - no pictures of puppies and/or kittens.

The hard part is fitting the info and message into a clear and concise format.

It must be appealing both to pet owners and vets (who are our primary source of patients through referrals).

It should covey WARMTH, COMPASSION, PROFESSIONALISM, and EXPERTISE.

Please look at our website www.TrellisAnimalRespite.com for more info

We have until now used maroon and copper for colors - to reflect the "sunset" of the pets life. BUT are now changing to Navy, Teal and White to reflect calm, trust and competence.

We will use the same logo recolored.

Existing brochure and new logo are attached.

PLEASE ask questions!!
Updates

We have a library of stock images you are welcome to use. All have been legally acquired and we have the right to use them. You DO NOT have to use them, just sending along in case you wish to. https://www.filecrate.example/sh/qk4vrm82zd1pyno/KLQ7Ztbn-Rrfx2mh9sWpYJ4Dc?dl=0

Our colors are NAVY, TEAL and WHITE. For your reference, the navy we use is 99/87/44/55 (CMYK) The Teal we use is 76/11/44/0 (CMYK) Thank you!

Designers -- pleaseuse pictures of older pets (no puppies or kittens). Below is a link to stock photos we own that would be appropriate for use in the brochure. https://www.filecrate.example/sh/w274m6t9pxkr5da/KLRn3GsfwlTVBXEPcq_8ZNj5u?dl=0 THANK YOU!

Designers -- I would VERY much like to include a photo of a pet in a wheel chair. I have personal photos as well as (purchased) stock photos for this purpose which can be found at http://lnk.example/TARHC-Pets-in-Wheelchairs Thank you!!

Today is the last day! Many of you have submitted beautiful designs and others are rolling in. I am so appreciative of your time and energy!! Please do not let the deadline pass without YOUR very BEST entry being submitted!! Thank you! - Miriam & All of us at Trellis Animal Respite & Home Care

Target Market(s)

Pet Owners and Veterinarians

Industry/Entity Type

Pet Care

Font styles to use
Serif

Colors
0455a3
33b8a4
ffffff

Requirements
Must have
• Our logo and information about our services. Pictures of pets. Our contact info. PLEASE NOTE: this is a 2 sided brochure. Please submit both inside and outside.
Should not have
• puppies, kittens - anything off message

```html
<!DOCTYPE html>
<html lang="en">
<head>
<meta charset="utf-8">
<title>Trellis Animal Respite &amp; Home Care – Trifold Brochure</title>
<link rel="stylesheet" href="https://fonts.googleapis.com/css2?family=Playfair+Display:wght@400;700&family=Tinos:wght@400;700&display=swap">
<style>
  :root{
    --navy:#0f1d3b;
    --teal:#25b6a0;
    --white:#ffffff;
    --ink:#1d2330;
    --rule:#c9ccd2;
    --display:"Playfair Display", Georgia, serif;
    --body:"Tinos", "Times New Roman", serif;
  }
  *{box-sizing:border-box;margin:0;padding:0}
  html,body{width:1000px;height:1200px;overflow:hidden;background:var(--white)}
  body{position:relative;font-family:var(--body);color:var(--ink)}

  .sheet{position:absolute;left:106px;width:789px;border:1px solid var(--rule);overflow:hidden;background:var(--white)}
  .sheet--outside{top:38px;height:557px}
  .sheet--inside{top:608px;height:559px}
  .panel{position:absolute;top:0;width:263px;height:100%;overflow:hidden}
  .panel:nth-child(1){left:0}
  .panel:nth-child(2){left:263px}
  .panel:nth-child(3){left:526px}
  .panel-bg{position:absolute;inset:0;width:100%;height:100%}
  .fold{position:absolute;top:0;bottom:0;width:1px;background:var(--rule)}

  .photo{position:absolute}
  .label{position:absolute;background:var(--navy);color:var(--white);font-family:var(--display);font-size:19px;line-height:1;padding:9px 14px 9px 28px;transform:rotate(-6deg);transform-origin:left bottom;white-space:nowrap}
  .label--light{background:var(--white);color:var(--navy)}

  .paws{list-style:none}
  .paws li{position:relative;padding-left:17px;font-size:10.5px;line-height:14px}
  .paws li svg{position:absolute;left:0;top:2px;width:10px;height:10px;fill:var(--navy)}
  .paws--white li svg{fill:var(--white)}
  .copy{font-size:10.5px;line-height:14px}

  /* outside */
  .believe-list{position:absolute;left:30px;top:80px;width:215px;color:var(--navy)}
  .believe-list li{margin-bottom:7px}

  .contact{position:absolute;left:23px;top:192px;font-size:10.5px;line-height:14px;color:var(--navy)}
  .contact strong{font-weight:700}
  .web{position:absolute;left:23px;top:334px;font-size:10.5px;color:var(--navy);font-weight:700}
  .web-row{display:flex;align-items:center;gap:4px;height:20px;margin-bottom:1px}
  .web-icon{width:16px;height:16px;border-radius:2px;background:var(--teal)}
  .web-icon--navy{background:var(--navy)}

  .brand{position:absolute;left:26px;top:24px;display:flex;align-items:center;gap:8px;color:var(--white);font-family:var(--display);font-size:13px;line-height:14px}
  .brand-mark{width:34px;height:34px;border-radius:50%;background:var(--teal)}
  .tagline{position:absolute;left:0;top:119px;width:263px;text-align:center;font-family:var(--body);font-weight:700;font-size:11.5px;line-height:13px;color:var(--navy);transform:rotate(-6deg)}
  .cover-title{position:absolute;left:0;top:486px;width:263px;text-align:center;font-family:var(--display);color:var(--white);font-size:18px;line-height:21px;transform:rotate(-6deg)}
  .cover-rule{position:absolute;left:104px;top:538px;width:55px;height:2px;background:var(--white);transform:rotate(-6deg)}

  /* inside */
  .palliative-copy{position:absolute;left:33px;top:150px;width:200px;color:var(--navy)}
  .palliative-copy p{margin-bottom:10px}
  .subhead{font-family:var(--body);font-weight:700;font-size:12.5px;line-height:14px;color:var(--navy);margin:4px 0 4px}
  .palliative-copy .paws li{margin-bottom:7px}

  .services{position:absolute;left:24px;top:76px;width:215px;color:var(--navy)}
  .services p{margin-bottom:11px}
  .services .paws li{margin-bottom:7px}

  .extras{position:absolute;left:22px;top:30px;width:220px;color:var(--navy)}
  .extras .paws li{margin-bottom:7px}
  .team{position:absolute;left:40px;top:330px;width:200px;color:var(--white)}
  .team .lead{font-weight:700;font-size:10.5px;line-height:13px;margin-bottom:5px;text-align:center}
  .team .paws li{margin-bottom:7px}
</style>
</head>
<body>
<svg width="0" height="0" style="position:absolute" aria-hidden="true">
  <symbol id="paw" viewBox="0 0 20 20">
    <ellipse cx="10" cy="14" rx="5" ry="4.2"/>
    <ellipse cx="3.6" cy="8.4" rx="2" ry="2.6"/>
    <ellipse cx="7.8" cy="4.4" rx="2" ry="2.6"/>
    <ellipse cx="12.2" cy="4.4" rx="2" ry="2.6"/>
    <ellipse cx="16.4" cy="8.4" rx="2" ry="2.6"/>
  </symbol>
</svg>

<!-- OUTSIDE -->
<section class="sheet sheet--outside">
  <div class="panel panel--believe">
    <svg class="panel-bg" viewBox="0 0 263 557" preserveAspectRatio="none" aria-hidden="true">
      <polygon points="0,70 263,0 263,400 0,470" fill="var(--teal)"/>
    </svg>
    <div class="photo" role="img" aria-label="Photo of a calm senior cat lying down" style="left:0;top:400px;width:263px;height:157px;background:linear-gradient(180deg,#f3f3f3,#e4e1dc);clip-path:polygon(0 44%,100% 0,100% 100%,0 100%)"></div>
    <div class="label" style="left:0;top:48px">We Believe</div>
    <ul class="paws believe-list">
      <li><svg><use href="#paw"/></svg>That animals are conscious beings, capable of thought, feeling, emotion and choice</li>
      <li><svg><use href="#paw"/></svg>That each animal is an individual with his or her unique needs and wishes</li>
      <li><svg><use href="#paw"/></svg>That all pets deserve to be pain-free</li>
      <li><svg><use href="#paw"/></svg>That the principles of human hospice and palliative care are equally powerful when applied to animals</li>
      <li><svg><use href="#paw"/></svg>That an interdisciplinary team is essential to addressing the needs of pets and their families through aging and illness</li>
      <li><svg><use href="#paw"/></svg>That quality of life is subjective, best evaluated by the family who knows and loves the animal</li>
      <li><svg><use href="#paw"/></svg>That there isn't one answer that is right for every animal or every family</li>
    </ul>
  </div>

  <div class="panel panel--contact">
    <div class="photo" role="img" aria-label="Photo of an older golden dog resting its head on a blanket" style="left:0;top:0;width:263px;height:150px;background:linear-gradient(160deg,#d9d4cc,#b67a3c 55%,#e9e7e3);clip-path:polygon(0 0,100% 0,100% 80%,0 100%)"></div>
    <div class="label" style="left:0;top:150px">Contact Us</div>
    <address class="contact" style="font-style:normal">
      Trellis Animal Respite &amp; Home Care<br>
      48 Orchard Mill Lane<br>
      Suite 210<br>
      Fernbrook, MA 01990<br>
      <strong>(555) 014-7220</strong><br>
      <strong>info@TrellisAnimalRespite.com</strong>
    </address>
    <div class="label" style="left:0;top:292px">On the Web</div>
    <div class="web">
      <div class="web-row"><span class="web-icon"></span>www.TrellisAnimalRespite.com</div>
      <div class="web-row"><span class="web-icon web-icon--navy"></span>TrellisAnimalRespite</div>
      <div class="web-row"><span class="web-icon web-icon--navy"></span><span class="web-icon"></span><span class="web-icon web-icon--navy"></span>&nbsp;TrellisRespite</div>
    </div>
    <div class="photo" role="img" aria-label="Photo of a grey tabby cat looking upward" style="left:0;top:430px;width:263px;height:127px;background:linear-gradient(180deg,#2a2624,#6d625a 60%,#1c1917);clip-path:polygon(0 20%,100% 0,100% 100%,0 100%)"></div>
  </div>

  <div class="panel panel--cover" style="background:var(--navy)">
    <div class="brand"><span class="brand-mark"></span><span>Trellis Animal Respite<br>&amp; Home Care</span></div>
    <div class="photo" role="img" aria-label="Photo of an older beagle cuddled close to its owner" style="left:0;top:150px;width:263px;height:350px;background:linear-gradient(135deg,#e7d7c4,#c58c55 45%,#f2ece4);clip-path:polygon(0 8%,100% 0,100% 92%,0 100%)"></div>
    <svg class="panel-bg" viewBox="0 0 263 557" preserveAspectRatio="none" aria-hidden="true" style="pointer-events:none">
      <polygon points="0,125 263,98 263,148 0,175" fill="var(--teal)"/>
    </svg>
    <p class="tagline">Trellis Animal Respite &amp;<br>Home Care Skilled Home Care for<br>Ill, Elderly and Special Needs Animals</p>
    <p class="cover-title">Compassionate<br>Support for Families</p>
    <span class="cover-rule"></span>
  </div>
</section>

<!-- INSIDE -->
<section class="sheet sheet--inside">
  <div class="panel panel--palliative">
    <div class="photo" role="img" aria-label="Photo of a cat using a mobility wheelchair on a lawn" style="left:0;top:0;width:263px;height:100px;background:linear-gradient(180deg,#6f8a4a,#9cbc5c 55%,#7fa446)"></div>
    <div class="label" style="left:0;top:86px;font-size:18px;line-height:20px;padding:8px 18px 8px 28px;text-align:center">Palliative Care<br>&nbsp;&nbsp;&nbsp;and Hospice</div>
    <div class="palliative-copy copy">
      <p>Palliative Care seeks to relieve suffering and improve quality of life at all stages of illness, injury and disease, whether curable or not.</p>
      <p>Hospice is a special kind of Palliative Care focused on those with a life expectancy of less than one year.</p>
      <h3 class="subhead">Both Palliative Care<br>and Hospice:</h3>
      <ul class="paws">
        <li><svg><use href="#paw"/></svg>Focus on living fully</li>
        <li><svg><use href="#paw"/></svg>Recognize and address all suffering ~ physical, emotional, social and spiritual</li>
        <li><svg><use href="#paw"/></svg>Use a team approach to meet the needs of the animal and his or her family</li>
        <li><svg><use href="#paw"/></svg>Affirm life while viewing death as a natural, normal process</li>
      </ul>
    </div>
    <div class="photo" role="img" aria-label="Photo of a senior beagle standing in a rear-support wheelchair" style="left:28px;top:415px;width:210px;height:125px;background:radial-gradient(ellipse at 55% 45%,#c99a6a,#e8e2dc 70%,#ffffff)"></div>
    <svg class="panel-bg" viewBox="0 0 263 559" preserveAspectRatio="none" aria-hidden="true" style="pointer-events:none">
      <polygon points="0,532 263,505 263,559 0,559" fill="var(--navy)"/>
    </svg>
  </div>

  <div class="panel panel--services">
    <svg class="panel-bg" viewBox="0 0 263 559" preserveAspectRatio="none" aria-hidden="true">
      <polygon points="0,20 263,0 263,540 0,559" fill="var(--teal)"/>
    </svg>
    <div class="label" style="left:0;top:26px">Our Services</div>
    <div class="services copy">
      <p>At Trellis Animal Respite &amp; Home Care, our only goal is to support you in providing the very best care for your beloved companion in your own home.</p>
      <p>We are here for you 24 hours a day, every day of the year.</p>
      <p>We work as a team to address the needs of your entire family. We come with no agenda and no prescribed plan, but rather follow your needs and wishes as they evolve and change over time.</p>
      <h3 class="subhead">Some of the services we offer are:</h3>
      <ul class="paws">
        <li><svg><use href="#paw"/></svg>Visiting and support</li>
        <li><svg><use href="#paw"/></svg>Administration of medication &amp; fluids</li>
        <li><svg><use href="#paw"/></svg>Overnight and respite care</li>
        <li><svg><use href="#paw"/></svg>Check-ins, exercise and play</li>
        <li><svg><use href="#paw"/></svg>Assistance evaluating pain, quality of life, and end of life choices</li>
        <li><svg><use href="#paw"/></svg>Coordination of care with your vet and other care professionals</li>
        <li><svg><use href="#paw"/></svg>Home cooked meals and treats</li>
        <li><svg><use href="#paw"/></svg>Transportation and errand running</li>
        <li><svg><use href="#paw"/></svg>Equipment and supplies</li>
        <li><svg><use href="#paw"/></svg>Funerals and memorials</li>
        <li><svg><use href="#paw"/></svg>Bereavement support</li>
      </ul>
    </div>
  </div>

  <div class="panel panel--team">
    <svg class="panel-bg" viewBox="0 0 263 559" preserveAspectRatio="none" aria-hidden="true">
      <polygon points="0,320 263,290 263,559 0,559" fill="var(--navy)"/>
    </svg>
    <div class="extras">
      <h3 class="subhead">Our skilled team members can<br>also provide:</h3>
      <ul class="paws">
        <li><svg><use href="#paw"/></svg>Massage and Gentle Touch</li>
        <li><svg><use href="#paw"/></svg>Cold LASER Treatments</li>
        <li><svg><use href="#paw"/></svg>Reiki</li>
        <li><svg><use href="#paw"/></svg>Passive Range of Motion (PROM)</li>
        <li><svg><use href="#paw"/></svg>Rehabilitation Support</li>
        <li><svg><use href="#paw"/></svg>Grooming</li>
        <li><svg><use href="#paw"/></svg>Essential Oils</li>
        <li><svg><use href="#paw"/></svg>Floral Essences</li>
        <li><svg><use href="#paw"/></svg>Aroma Therapy</li>
        <li><svg><use href="#paw"/></svg>Music Therapy</li>
        <li><svg><use href="#paw"/></svg>Pet Therapy</li>
      </ul>
    </div>
    <div class="photo" role="img" aria-label="Photo of an older mixed-breed dog outdoors" style="left:165px;top:217px;width:97px;height:62px;background:linear-gradient(135deg,#7fa35a,#a0673a 50%,#6c8f48)"></div>
    <div class="label label--light" style="left:118px;top:282px">Our Team</div>
    <div class="team">
      <p class="lead">Lead by Miriam Calloway, C.T.<br>our interdisciplinary team includes:</p>
      <ul class="paws paws--white">
        <li><svg><use href="#paw"/></svg>Certified Thanatologist</li>
        <li><svg><use href="#paw"/></svg>Certified Veterinary Technicians</li>
        <li><svg><use href="#paw"/></svg>Interfaith Spiritual Advisor</li>
        <li><svg><use href="#paw"/></svg>Certified Small Animal Massage Therapist</li>
        <li><svg><use href="#paw"/></svg>Animal Care Specialists</li>
        <li><svg><use href="#paw"/></svg>Hospice Assistants</li>
        <li><svg><use href="#paw"/></svg>Client Care Coordinator</li>
      </ul>
    </div>
  </div>
  <span class="fold" style="left:525px"></span>
</section>
</body>
</html>
```